TLK Electricial Contracting Services

Hi guys, after a design for my small electrical company, have logo design files to be incorporated into the layout, the basic concept is electrical contracting services for residential, commercial, industrial & data services, image is clean clear and strong,

Card format is to have a nice clean logo on front,with maybe the Residential – commercial – industrial - data, followed with licensed & insured, followed by contact details on backside of the card.

Target Market(s)

Residential, commercial, industrial sectors.

Industry/Entity Type

Electrical

Contact Information for Business Card

TLK logo,
Residential – commercial – industrial - data
REC: 61307
Email: tlk@vornamail.net.au
Phone: 0487 352 019

Requirements
Must have
• Clean & strong design.
Nice to have
• If possible, I would like the logo colours inverted so the text is orange and the background is black on the front of the card, then the backside of the card be the reverse colour
Should not have
• No Sparks, lightning bolts,

```html
<!DOCTYPE html>
<html lang="en">
<head>
<meta charset="utf-8">
<title>TLK Electrical – Business Card</title>
<link rel="stylesheet" href="https://fonts.googleapis.com/css2?family=Exo+2:wght@400;500;700;800&display=swap">
<style>
  :root {
    --orange: #f47a1f;
    --black: #0d0d0d;
    --stage: #ecebe8;
    --card-w: 500px;
    --card-h: 300px;
  }
  * { box-sizing: border-box; margin: 0; padding: 0; }
  html, body {
    width: 1200px;
    height: 800px;
    overflow: hidden;
    background: var(--stage);
    font-family: "Exo 2", Arial, sans-serif;
  }
  .stage {
    position: relative;
    width: 1200px;
    height: 800px;
  }
  .card {
    position: absolute;
    top: 250px;
    width: var(--card-w);
    height: var(--card-h);
    overflow: hidden;
    border-radius: 3px;
    box-shadow: 0 6px 18px rgba(0,0,0,0.18);
  }

  /* ---------- Contact side (orange) ---------- */
  .card--contact {
    left: 70px;
    background: var(--orange);
    color: var(--black);
  }
  .card--contact .corner-disc {
    position: absolute;
    width: 130px;
    height: 130px;
    border-radius: 50%;
    background: var(--black);
    top: -65px;
    right: -5px;
  }
  .card--contact .brand {
    position: absolute;
    left: 30px;
    top: 38px;
  }
  .brand-name {
    font-weight: 800;
    line-height: 1;
    letter-spacing: 2px;
  }
  .brand-sub {
    font-weight: 700;
    line-height: 1;
    letter-spacing: 0.2px;
  }
  .card--contact .brand-name { font-size: 62px; }
  .card--contact .brand-sub { font-size: 14px; margin-top: 4px; }

  .services {
    position: absolute;
    left: 36px;
    top: 150px;
    list-style: none;
    font-size: 19px;
    font-weight: 500;
    line-height: 1.18;
  }
  .services li::before {
    content: "";
    display: inline-block;
    width: 6px;
    height: 6px;
    border-radius: 50%;
    background: var(--black);
    margin-right: 4px;
    vertical-align: middle;
  }
  .licence {
    position: absolute;
    left: 44px;
    top: 248px;
    font-size: 15px;
    font-weight: 500;
  }
  .contact {
    position: absolute;
    left: 280px;
    top: 112px;
    list-style: none;
  }
  .contact li {
    display: flex;
    align-items: center;
    gap: 8px;
    font-weight: 500;
    margin-bottom: 6px;
  }
  .contact .phone { font-size: 22px; letter-spacing: 0.5px; }
  .contact .email { font-size: 17px; }
  .contact svg { width: 16px; height: 16px; flex: none; fill: var(--black); }

  /* ---------- Logo side (black) ---------- */
  .card--logo {
    left: 630px;
    background: var(--black);
    color: var(--orange);
    text-align: center;
  }
  .card--logo .edge-disc {
    position: absolute;
    width: 120px;
    height: 120px;
    border-radius: 50%;
    background: var(--orange);
    left: -60px;
    top: 100px;
  }
  .card--logo .brand {
    position: absolute;
    left: 70px;
    right: 30px;
    top: 48px;
  }
  .card--logo .brand-name { font-size: 78px; }
  .card--logo .brand-sub { font-size: 18px; margin-top: 4px; }
  .tagline {
    position: absolute;
    left: 70px;
    right: 30px;
    top: 190px;
    font-size: 15px;
    font-weight: 400;
    line-height: 1.3;
    letter-spacing: 0.3px;
  }
</style>
</head>
<body>
<main class="stage">

  <section class="card card--contact" aria-label="Business card contact side">
    <div class="corner-disc"></div>
    <div class="brand">
      <div class="brand-name">TLK</div>
      <div class="brand-sub">Tate Lowell Kerr Electrical</div>
    </div>
    <ul class="services">
      <li>Residential</li>
      <li>Commercial</li>
      <li>Industrial</li>
      <li>Data</li>
    </ul>
    <p class="licence">REC: 61307</p>
    <ul class="contact">
      <li class="phone">
        <svg viewBox="0 0 16 16" aria-hidden="true">
          <path d="M3.5 1.5l2.5 0 1 3.5-1.6 1.2a9 9 0 0 0 4.4 4.4L11 9l3.5 1v2.5c0 1-1 2-2 2C6.5 14.5 1.5 9.5 1.5 3.5c0-1 1-2 2-2z"/>
        </svg>
        0487 352 019
      </li>
      <li class="email">
        <svg viewBox="0 0 16 16" aria-hidden="true">
          <path d="M1 4h14v9H1z M1 4l7 5 7-5" fill="none" stroke="#0d0d0d" stroke-width="1.6"/>
        </svg>
        tlk@vornamail.net.au
      </li>
    </ul>
  </section>

  <section class="card card--logo" aria-label="Business card logo side">
    <div class="edge-disc"></div>
    <div class="brand">
      <div class="brand-name">TLK</div>
      <div class="brand-sub">Tate Lowell Kerr Electrical</div>
    </div>
    <p class="tagline">Electrical contracting services for residential,<br>commercial, industrial &amp; data services.</p>
  </section>

</main>
</body>
</html>
```